BRIVAN 2026 Flyer for Conference

BRIVAN needs a design for a 1-page flyer that we will hand out at an upcoming event & then later post online as a pdf. There are 3 elements which need to be on the flyer:

1) A logo. This should be prominent on the design (e.g., in the middle). The flyer should use the colors that are in that logo (e.g., for accents, design elements, and/or text; not all of these have to be used):
Dark blue: #185577
Med blue: #327C9A
Teal: #4EB1C2
Light Teal: #9EDBE6

2) The conference theme -- Oceans of Knowledge: Diving into Information Literacy -- should be at the flyer's top.

3) Finally, these six tracks should be listed below the theme and the logo (it's font size should be at least a couple sizes smaller than the size used for the theme):
- Pearls of Pedagogy: Teaching Techniques that Work
- The Depth Gauge: Measuring Instructional Impact
- Techtonic Shifts: Innovation and Educational Technology
- Captain's Log: Navigating Leadership in Library Instruction
- Swimming Together: Collaborating with Others
- The Bermuda Triangle: Exploring (Seemingly) Eternal Challenges

Font styles to use
Sans Serif

Colors
0094D4
00A9DD
6FCCEA
C7EBF8
E9F6FB

Requirements
Must have
• The 3 elements listed in the description: 1) the logo, 2) the text of the theme and 3) the text for the tracks.

```html
<!DOCTYPE html>
<html lang="en">
<head>
<meta charset="utf-8">
<title>BRIVAN 2026 – Oceans of Knowledge</title>
<link href="https://fonts.googleapis.com/css2?family=Josefin+Sans:wght@400;600;700&family=Poppins:wght@400;500;600;700;800&display=swap" rel="stylesheet">
<style>
  :root{
    --dark-blue:#185577;
    --med-blue:#327C9A;
    --teal:#4EB1C2;
    --light-teal:#9EDBE6;
    --navy:#0f3347;
    --pill:#143e55;
    --white:#ffffff;
    --ink:#1c3e52;
  }
  *{box-sizing:border-box;margin:0;padding:0}
  html,body{width:831px;height:1200px;overflow:hidden;background:#fff}
  .flyer{position:relative;width:831px;height:1200px;overflow:hidden;background:var(--white);font-family:"Poppins",sans-serif}

  .hero-photo{position:absolute;left:0;top:0;width:831px;height:720px;
    background:linear-gradient(180deg,#0d2b3d 0%,#123e56 22%,#1b6683 45%,#2a8fab 65%,#3aa9c2 80%,#59c1d2 100%)}
  .sky-photo{position:absolute;left:0;bottom:0;width:831px;height:230px;
    background:linear-gradient(180deg,#ffffff 0%,#e4f1fa 30%,#a9d6ee 62%,#6ccbe0 78%,#32b7cc 90%,#1fa6bf 100%)}

  .wave{position:absolute;left:0;top:480px;width:831px;height:250px}

  .brand{position:absolute;left:50px;top:92px;width:222px;display:flex;flex-direction:column;align-items:center;text-align:center}
  .brand-dot{width:40px;height:40px;border-radius:50%;background:var(--teal);margin-bottom:8px}
  .brand-name{font-family:"Poppins",sans-serif;font-weight:700;font-size:26px;line-height:1.1;color:var(--light-teal);letter-spacing:.5px;white-space:nowrap}
  .brand-meta{margin-top:6px;font-family:"Josefin Sans",sans-serif;font-size:10px;letter-spacing:1.6px;color:var(--light-teal);font-weight:600;white-space:nowrap}

  .theme{position:absolute;left:282px;top:62px;color:var(--white)}
  .theme-lead{font-family:"Josefin Sans",sans-serif;font-weight:700;font-size:46px;line-height:1;color:var(--teal);letter-spacing:1px}
  .theme-main{font-family:"Poppins",sans-serif;font-weight:800;font-size:78px;line-height:1;margin-top:4px;letter-spacing:0}
  .theme-sub{font-family:"Josefin Sans",sans-serif;font-weight:600;font-size:20px;letter-spacing:2.8px;margin-top:4px;white-space:nowrap}

  .tracks-heading{position:absolute;left:0;top:676px;width:831px;text-align:center;font-family:"Josefin Sans",sans-serif;font-size:31px;letter-spacing:3px;color:var(--ink)}
  .tracks-heading .light{font-weight:400;color:var(--teal)}
  .tracks-heading .bold{font-weight:700}

  .tracks{position:absolute;left:44px;top:728px;display:flex;gap:13px}
  .track{position:relative;width:113px;height:306px;border-radius:57px;background:var(--pill);padding:138px 10px 0 18px}
  .track-icon{position:absolute;left:50%;top:-6px;transform:translateX(-50%);width:122px;height:122px;border-radius:50%;background:#cdeef3;display:flex;align-items:center;justify-content:center}
  .track-icon::before{content:"";position:absolute;inset:10px;border-radius:50%;background:var(--white)}
  .track-icon .disc{position:relative;width:92px;height:92px;border-radius:50%;background:var(--teal);display:flex;align-items:center;justify-content:center}
  .track-icon svg{width:46px;height:46px}
  .track-title{font-weight:700;font-size:15.5px;line-height:1.2;color:var(--teal)}
  .track-text{font-weight:400;font-size:12.5px;line-height:1.25;color:var(--white);margin-top:9px}
</style>
</head>
<body>
<main class="flyer">
  <div class="hero-photo" role="img" aria-label="Underwater photograph of a sea turtle swimming beneath the ocean surface over a reef"></div>
  <div class="sky-photo" role="img" aria-label="Tropical seascape with a bright cloudy sky, green island and turquoise water"></div>

  <svg class="wave" viewBox="0 0 831 250" preserveAspectRatio="none" aria-hidden="true">
    <path d="M0 150 C160 40 330 70 470 100 C620 130 720 80 831 30 L831 250 L0 250Z" fill="#2ec0db"/>
    <path d="M0 175 C150 80 320 95 470 125 C620 150 730 110 831 70 L831 250 L0 250Z" fill="#4fcde2"/>
    <path d="M0 205 C130 120 300 110 470 140 C620 168 740 140 831 120 L831 250 L0 250Z" fill="#ffffff"/>
  </svg>

  <div class="brand">
    <span class="brand-dot"></span>
    <span class="brand-name">BRIVAN 2026</span>
    <span class="brand-meta">HARBOR CITY, VA · MAY 7-9</span>
  </div>

  <header class="theme">
    <div class="theme-lead">OCEANS OF</div>
    <h1 class="theme-main">KNOWLEDGE</h1>
    <div class="theme-sub">DIVING INTO INFORMATION LITERACY</div>
  </header>

  <h2 class="tracks-heading"><span class="light">OUR</span> <span class="bold">SIX TRACKS</span></h2>

  <section class="tracks">
    <article class="track">
      <div class="track-icon"><div class="disc">
        <svg viewBox="0 0 46 46" fill="none" stroke="#fff" stroke-width="2.4" stroke-linecap="round"><circle cx="23" cy="22" r="7" fill="#fff"/><path d="M8 30 Q23 40 38 30"/><path d="M23 6v4M12 10l3 3M34 10l-3 3"/></svg>
      </div></div>
      <div class="track-title">Pearls of Pedagogy</div>
      <div class="track-text">Teaching Techniques that Work</div>
    </article>
    <article class="track">
      <div class="track-icon"><div class="disc">
        <svg viewBox="0 0 46 46" fill="none" stroke="#fff" stroke-width="2.4" stroke-linecap="round" stroke-linejoin="round"><rect x="10" y="9" width="26" height="28" rx="2" fill="#fff" stroke="none"/><path d="M23 14v18M19 18l4-4 4 4M19 28l4 4 4-4" stroke="#4EB1C2"/></svg>
      </div></div>
      <div class="track-title">The Depth Gauge</div>
      <div class="track-text">Measuring Instructional Impact</div>
    </article>
    <article class="track">
      <div class="track-icon"><div class="disc">
        <svg viewBox="0 0 46 46" fill="#fff"><path d="M6 16h22l12 6H6z"/><path d="M6 25h34v5H18z"/><path d="M6 33h34v4H6z"/></svg>
      </div></div>
      <div class="track-title">Techtonic Shifts</div>
      <div class="track-text">Innovation &amp; Educational Technology</div>
    </article>
    <article class="track">
      <div class="track-icon"><div class="disc">
        <svg viewBox="0 0 46 46" fill="none" stroke="#fff" stroke-width="2.6" stroke-linecap="round"><circle cx="23" cy="23" r="9"/><circle cx="23" cy="23" r="3" fill="#fff"/><path d="M23 8v6M23 32v6M8 23h6M32 23h6M12.5 12.5l4 4M29.5 29.5l4 4M33.5 12.5l-4 4M16.5 29.5l-4 4"/></svg>
      </div></div>
      <div class="track-title">Captain's Log</div>
      <div class="track-text">Navigating Leadership in Library Instruction</div>
    </article>
    <article class="track">
      <div class="track-icon"><div class="disc">
        <svg viewBox="0 0 46 46" fill="none" stroke="#fff" stroke-width="2.6" stroke-linecap="round"><circle cx="28" cy="13" r="4" fill="#fff" stroke="none"/><path d="M12 25l9-7 6 5"/><path d="M6 31q4-3 8 0t8 0 8 0 8 0"/><path d="M6 37q4-3 8 0t8 0 8 0 8 0"/></svg>
      </div></div>
      <div class="track-title">Swimming Together</div>
      <div class="track-text">Collaborating with Others</div>
    </article>
    <article class="track">
      <div class="track-icon"><div class="disc">
        <svg viewBox="0 0 46 46" fill="none" stroke="#fff" stroke-width="2.6" stroke-linejoin="round" stroke-linecap="round"><path d="M10 12L36 9 27 36Z"/><circle cx="10" cy="12" r="3" fill="#fff"/><circle cx="36" cy="9" r="3" fill="#fff"/><circle cx="27" cy="36" r="3" fill="#fff"/></svg>
      </div></div>
      <div class="track-title">The Bermuda Triangle</div>
      <div class="track-text">Exploring (Seemingly) Eternal Challenges</div>
    </article>
  </section>
</main>
</body>
</html>
```